Fern Lattice Table & Chair Rentals

We need a business card for a table and chair rental company. We rent tables and chairs for weddings, funerals, business events and parties. We want something that looks clean and elegant while not being too busy. We would like colors in the green and blue hues and avoiding anything orange. We want to make sure the font is large enough to be seen easily.

Target Market(s)

Wedding & Event Rentals

Industry/Entity Type

Events

Contact Information for Business Card

Fern Lattice, sales@fernlatticerentals.com, fernlatticerentals.com, 360-555-0182

Requirements
Must have
• Easy to read font
Should not have
• Orange anywhere in the design

```html
<!DOCTYPE html>
<html lang="en">
<head>
<meta charset="utf-8">
<title>Fern Lattice Table &amp; Chair Rentals – Business Card</title>
<link rel="stylesheet" href="https://fonts.googleapis.com/css2?family=Arimo:wght@400;700&display=swap">
<style>
  :root {
    --page-bg: #e6e9e8;
    --card-bg: #ffffff;
    --accent: #4fa88a;
    --accent-deep: #2f7f86;
    --ink: #1e2a2a;
    --ink-soft: #4a5555;
    --rule: #6a7474;
  }
  * { margin: 0; padding: 0; box-sizing: border-box; }
  html, body {
    width: 1200px;
    height: 902px;
    overflow: hidden;
    background: var(--page-bg);
    font-family: "Arimo", Arial, sans-serif;
  }
  .card {
    position: absolute;
    left: 240px;
    width: 720px;
    height: 411px;
    overflow: hidden;
    box-shadow: 0 8px 24px rgba(0,0,0,0.16);
  }
  .card--back { top: 28px; background: var(--accent); }
  .card--front { top: 463px; background: var(--card-bg); }
  .card__corners {
    position: absolute;
    inset: 0;
    width: 100%;
    height: 100%;
  }
  .card__corners .accent { fill: var(--accent); }
  .card__corners .accent-deep { fill: var(--accent-deep); }
  .card__corners .paper { fill: var(--card-bg); }

  /* reverse side */
  .back-brand {
    position: absolute;
    left: 110px;
    top: 150px;
  }
  .back-brand__name {
    font-size: 62px;
    font-weight: 700;
    line-height: 1;
    color: var(--ink);
  }
  .back-brand__tagline {
    margin-top: 10px;
    font-size: 26px;
    color: var(--ink);
  }

  /* front side */
  .brand {
    position: absolute;
    left: 60px;
    top: 66px;
  }
  .brand__name {
    font-size: 48px;
    font-weight: 700;
    line-height: 1;
    color: var(--ink);
  }
  .brand__tagline {
    margin-top: 8px;
    font-size: 20px;
    color: var(--ink-soft);
  }
  .company {
    position: absolute;
    left: 60px;
    top: 180px;
    font-size: 24px;
    color: var(--ink);
    white-space: nowrap;
  }
  .divider {
    position: absolute;
    left: 400px;
    top: 236px;
    width: 1px;
    height: 110px;
    background: var(--rule);
  }
  .contact {
    position: absolute;
    left: 420px;
    top: 240px;
    list-style: none;
  }
  .contact__item {
    display: flex;
    align-items: center;
    gap: 10px;
    height: 34px;
    font-size: 16px;
    color: var(--ink);
    white-space: nowrap;
  }
  .contact__icon { width: 16px; height: 16px; flex: none; }
  .contact__icon .fill { fill: var(--ink); }
  .contact__icon .outline { fill: none; stroke: var(--ink); stroke-width: 2; }
</style>
</head>
<body>
  <section class="card card--back" aria-label="Card reverse">
    <svg class="card__corners" viewBox="0 0 720 411" aria-hidden="true">
      <polygon class="paper" points="0,0 150,0 0,190"/>
      <polygon class="paper" points="640,0 720,0 720,60"/>
    </svg>
    <div class="back-brand">
      <div class="back-brand__name">Fern Lattice</div>
      <div class="back-brand__tagline">Table and Chair Rentals</div>
    </div>
  </section>

  <section class="card card--front" aria-label="Card front">
    <svg class="card__corners" viewBox="0 0 720 411" aria-hidden="true">
      <polygon class="accent" points="468,0 720,0 720,126"/>
      <polygon class="accent" points="0,302 0,411 248,411"/>
    </svg>

    <div class="brand">
      <div class="brand__name">Fern Lattice</div>
      <div class="brand__tagline">Table and Chair Rentals</div>
    </div>

    <div class="company">Fernlattice Event Rentals, LLC</div>

    <div class="divider"></div>

    <ul class="contact">
      <li class="contact__item">
        <svg class="contact__icon" viewBox="0 0 24 24" aria-hidden="true">
          <path class="fill" d="M6.6 10.8a15.1 15.1 0 0 0 6.6 6.6l2.2-2.2a1 1 0 0 1 1-.25 11.4 11.4 0 0 0 3.6.57 1 1 0 0 1 1 1V20a1 1 0 0 1-1 1A17 17 0 0 1 3 4a1 1 0 0 1 1-1h3.5a1 1 0 0 1 1 1c0 1.25.2 2.45.57 3.57a1 1 0 0 1-.25 1z"/>
        </svg>
        <span>360-555-0182</span>
      </li>
      <li class="contact__item">
        <svg class="contact__icon" viewBox="0 0 24 24" aria-hidden="true">
          <rect class="outline" x="3" y="4" width="18" height="12" rx="1"/>
          <rect class="fill" x="11" y="16" width="2" height="3"/>
          <rect class="fill" x="7" y="19" width="10" height="2"/>
        </svg>
        <span>www.fernlatticerentals.com</span>
      </li>
      <li class="contact__item">
        <svg class="contact__icon" viewBox="0 0 24 24" aria-hidden="true">
          <path class="outline" d="M2 6h20v12H2z"/>
          <path class="fill" d="M2 6l10 7 10-7z"/>
        </svg>
        <span>sales@fernlatticerentals.com</span>
      </li>
    </ul>
  </section>
</body>
</html>
```